Dental office stationary (letterhead, envelopes), business cards, presentation folders

Nothing too dental outside of the logo. I will need all stationary, presentation folders, business cards. Would prefer to stay in the colors of the logo

Gordon Patel, DDS
Bright Haven Dental Implant Center
555-318-2790
info@brighthavendental.example
4817 NW Maple Crest Rd Unit B
Lakeview, ST 00000

Also need appointment date and time
And cancellation policy
I want it to say “kindly ask for
A 48hr cancellation policy to avoid incurring a cancellation fee”

Industry/Entity Type

Dental

Colors
0054AA
0677BA
7BADD7
CADEEF
E8F1F8

Requirements
Must have
• Name of your office, name of doctor, address, phone number
Should not have
• Too much tooth/dental. Only the tooth in logo

```html
<!DOCTYPE html>
<html lang="en">
<head>
<meta charset="utf-8">
<title>Bright Haven Dental Implant Center – Business Card</title>
<link rel="stylesheet" href="https://fonts.googleapis.com/css2?family=Arimo:wght@400&family=Libre+Baskerville:wght@400&family=Marcellus&display=swap">
<style>
  :root {
    --backdrop: #3f3f3f;
    --teal: #17b89c;
    --sky: #17b5e6;
    --blue: #1a7fd0;
    --ink: #333333;
    --white: #ffffff;
    --brand: #1496c8;
  }
  * { box-sizing: border-box; margin: 0; padding: 0; }
  html, body {
    width: 1069px; height: 1200px; overflow: hidden;
    background: var(--backdrop);
  }
  .sheet {
    position: relative; width: 1069px; height: 1200px;
    display: flex; flex-direction: column; align-items: center; justify-content: center;
    gap: 60px;
  }
  .card {
    position: relative; width: 880px; height: 503px;
    border-radius: 26px; overflow: hidden;
  }
  .card--front { background: var(--teal); }
  .card--back { background: var(--white); }

  .wordmark {
    font-family: "Marcellus", serif; font-weight: 400;
    text-align: center; line-height: 1;
  }
  .wordmark__name { display: block; }
  .wordmark__tag { display: block; letter-spacing: 0.32em; }

  .card--front .wordmark {
    position: absolute; left: 20px; top: 212px; width: 330px;
    color: var(--white);
  }
  .card--front .wordmark__name { font-size: 46px; }
  .card--front .wordmark__tag { font-size: 13px; margin-top: 8px; }

  .emblem {
    position: absolute; right: 0; top: 0; width: 520px; height: 503px;
  }

  .contact {
    position: absolute; left: 500px; top: 140px; width: 360px;
    text-align: center; font-family: "Arimo", sans-serif; color: var(--ink);
  }
  .contact__name {
    font-family: "Libre Baskerville", serif; font-size: 29px; color: var(--blue);
    letter-spacing: 0.01em; white-space: nowrap;
  }
  .contact__title {
    font-size: 18px; color: var(--teal); text-align: right; margin-top: 2px; padding-right: 4px;
  }
  .contact__lines { font-size: 19px; line-height: 1.38; margin-top: 18px; white-space: nowrap; }
  .contact__lines + .contact__lines { margin-top: 20px; }

  .card--back .wordmark {
    position: absolute; left: 0; right: 0; top: 190px;
    color: var(--brand);
  }
  .card--back .wordmark__name { font-size: 84px; }
  .card--back .wordmark__tag { font-size: 22px; margin-top: 16px; }
</style>
</head>
<body>
<main class="sheet">
  <section class="card card--front">
    <div class="wordmark">
      <span class="wordmark__name">Bright Haven</span>
      <span class="wordmark__tag">DENTAL IMPLANT CENTER</span>
    </div>

    <svg class="emblem" viewBox="0 0 520 503" role="img" aria-label="Large decorative brand emblem in blue and teal behind the contact details">
      <defs>
        <radialGradient id="emblemGlow" cx="62%" cy="48%" r="62%">
          <stop offset="0" stop-color="#ffffff"/>
          <stop offset="0.62" stop-color="#ffffff"/>
          <stop offset="0.82" stop-color="#17b5e6"/>
          <stop offset="1" stop-color="#17b89c"/>
        </radialGradient>
      </defs>
      <path d="M130 0 H520 V503 H110 C40 430 10 330 20 240 C32 130 70 50 130 0 Z" fill="url(#emblemGlow)"/>
    </svg>

    <div class="contact">
      <p class="contact__name">GORDON PATEL</p>
      <p class="contact__title">DDS</p>
      <p class="contact__lines">4817 NW Maple Crest Rd Unit B<br>Lakeview, ST 00000</p>
      <p class="contact__lines">555-318-2790<br>info@brighthavendental.example<br>www.brighthavendental.example</p>
    </div>
  </section>

  <section class="card card--back">
    <div class="wordmark">
      <span class="wordmark__name">Bright Haven</span>
      <span class="wordmark__tag">DENTAL IMPLANT CENTER</span>
    </div>
  </section>
</main>
</body>
</html>
```